Business Card Design

We need a business card designed for our new company. Prefer a black card with white logo & writing.

Contact Information for Business Card

Ted Galloway, address: 7-4812 Fernhollow Road, Abbotsford, BC, V3K 8R2, Office Phone: 604-712-3390, Cell: 604-947-2164, Email: ted@resinworkshub.ca

Colors

Designer to choose only greyscale colors for use in the design.

```html
<!DOCTYPE html>
<html lang="en">
<head>
<meta charset="utf-8">
<title>Resin Works Hub – Business Card</title>
<link href="https://fonts.googleapis.com/css2?family=Montserrat:wght@400;500;600;700&display=swap" rel="stylesheet">
<style>
  :root {
    --page-bg: #dcdcdc;
    --card-dark: #262626;
    --card-light: #ffffff;
    --ink-light: #ffffff;
    --ink-dark: #222222;
    --pattern-light: #4a4a4a;
    --pattern-dark: #1c1c1c;
  }
  * { margin: 0; padding: 0; box-sizing: border-box; }
  html, body { width: 900px; height: 1200px; overflow: hidden; }
  body {
    background: var(--page-bg);
    font-family: "Montserrat", sans-serif;
    position: relative;
  }
  .card {
    position: absolute;
    left: 80px;
    width: 742px;
    height: 441px;
    border-radius: 22px;
    overflow: hidden;
    background: var(--card-dark);
    box-shadow: 0 10px 24px rgba(0,0,0,0.35);
  }
  .card-front { top: 131px; }
  .card-back { top: 638px; }

  .front-swoosh { position: absolute; inset: 0; }

  .holder { position: absolute; left: 37px; top: 48px; color: var(--ink-light); }
  .holder-name { font-size: 24px; font-weight: 600; letter-spacing: 0.2px; }
  .holder-role { font-size: 15px; font-weight: 400; margin-top: 4px; }

  .address {
    position: absolute; left: 38px; top: 234px;
    color: var(--ink-light); font-size: 16px; line-height: 21px;
  }
  .contacts {
    position: absolute; left: 37px; top: 298px;
    list-style: none; color: var(--ink-light); font-size: 15.5px;
  }
  .contacts li { display: flex; align-items: center; height: 26px; margin-bottom: 2px; }
  .contacts li:nth-child(2) { margin-bottom: 0; }
  .contacts svg { width: 15px; height: 15px; margin-right: 13px; fill: var(--ink-light); }

  .front-brand {
    position: absolute; left: 480px; top: 230px; width: 250px;
    text-align: center; color: var(--ink-dark);
    font-size: 24px; font-weight: 700; letter-spacing: 0.5px; line-height: 28px;
  }

  .back-pattern {
    position: absolute; inset: 0;
    background: linear-gradient(100deg, var(--pattern-light) 0%, #2e2e2e 35%, var(--pattern-dark) 60%, var(--pattern-dark) 100%);
  }
  .back-brand {
    position: absolute; left: 488px; top: 313px; width: 130px;
    text-align: center; color: var(--ink-light);
    font-size: 14px; font-weight: 700; letter-spacing: 0.4px; line-height: 16px;
  }
</style>
</head>
<body>

<section class="card card-front" aria-label="Business card front">
  <svg class="front-swoosh" viewBox="0 0 742 441" aria-hidden="true">
    <path d="M742 0 L612 0 C470 50 380 180 420 280 C450 360 530 410 610 441 L742 441 Z" fill="var(--card-light)"/>
    <path d="M595 20 C470 80 395 200 430 290 C455 360 520 405 590 435 C520 395 468 350 448 285 C420 200 480 90 595 20 Z" fill="var(--card-dark)"/>
  </svg>

  <div class="holder">
    <p class="holder-name">Ted Galloway</p>
    <p class="holder-role">Owner</p>
  </div>

  <p class="address">7-4812 Fernhollow Road,<br>Abbotsford, BC, V3K 8R2</p>

  <ul class="contacts">
    <li>
      <svg viewBox="0 0 24 24" aria-hidden="true"><path d="M6.6 10.8c1.4 2.8 3.8 5.1 6.6 6.6l2.2-2.2c.3-.3.7-.4 1-.2 1.1.4 2.3.6 3.6.6.6 0 1 .4 1 1V20c0 .6-.4 1-1 1C10.6 21 3 13.4 3 4c0-.6.4-1 1-1h3.5c.6 0 1 .4 1 1 0 1.3.2 2.5.6 3.6.1.3 0 .7-.2 1L6.6 10.8z"/></svg>
      604-712-3390
    </li>
    <li>
      <svg viewBox="0 0 24 24" aria-hidden="true"><path d="M16 1H8C6.9 1 6 1.9 6 3v18c0 1.1.9 2 2 2h8c1.1 0 2-.9 2-2V3c0-1.1-.9-2-2-2zm-4 21c-.8 0-1.5-.7-1.5-1.5S11.2 19 12 19s1.5.7 1.5 1.5S12.8 22 12 22zm4-4H8V4h8v14z"/></svg>
      604-947-2164
    </li>
    <li>
      <svg viewBox="0 0 24 24" aria-hidden="true"><path d="M2 5h20v2l-10 6L2 7V5zm0 4l10 6 10-6v10H2V9z"/></svg>
      ted@resinworkshub.ca
    </li>
    <li>
      <svg viewBox="0 0 24 24" aria-hidden="true"><path d="M12 2a10 10 0 1 0 0 20 10 10 0 0 0 0-20zm-1 17.9A8 8 0 0 1 4.1 10L9 15v1c0 1.1.9 2 2 2v1.9zm6.9-2.5c-.3-.8-1-1.4-1.9-1.4h-1v-3c0-.6-.4-1-1-1H8v-2h2c.6 0 1-.4 1-1V7h2c1.1 0 2-.9 2-2v-.4a8 8 0 0 1 2.9 12.8z"/></svg>
      www.resinworkshub.ca
    </li>
  </ul>

  <p class="front-brand">RESIN WORKS<br>HUB</p>
</section>

<section class="card card-back" aria-label="Business card back">
  <div class="back-pattern" role="img" aria-label="Repeating tone-on-tone pattern of the company mark across the card back"></div>
  <p class="back-brand">RESIN WORKS<br>HUB</p>
</section>

</body>
</html>
```